Business Card- Can you make it cool vs boring!

Need a refresh on my business card! Want it to be modern but simple, classic and a pop of coolness! we do senior living and it is boring. but that doesn't mean our business card have to look boring! Open to two sided cards. our website is www.Dunmere-PK.com

Target Market(s)

capital market

Industry/Entity Type

senior housing/ real estate

Contact Information for Business Card

logo/ name/ cell/ address/ www.Dunmere-PK.com/ space for a QR code

Requirements
Must have
• maybe a QR code (do not make prominent I may not use the QR so design where it can be taken out) that link to more about us/ landing page. needs to be modern but clean
Should not have
• clip art or script

```html
<!DOCTYPE html>
<html lang="en">
<head>
<meta charset="utf-8">
<title>Dunmere Living – Business Card</title>
<link rel="stylesheet" href="https://fonts.googleapis.com/css2?family=Arimo:wght@400;700&display=swap">
<style>
  :root {
    --rust: #b5562c;
    --rust-dark: #ad4f25;
    --rust-light: #ba5f33;
    --gold: #e6b45a;
    --ink: #4a4a4a;
    --muted: #777777;
    --paper: #ffffff;
    --backdrop: #e4e4e4;
    --rule: #bdbdbd;
  }
  * { box-sizing: border-box; margin: 0; padding: 0; }
  html, body { width: 1200px; height: 1200px; overflow: hidden; }
  body {
    background: var(--backdrop);
    font-family: "Arimo", Arial, sans-serif;
    position: relative;
  }
  .card {
    position: absolute;
    width: 688px;
    height: 393px;
  }
  .card--front { left: 267px; top: 159px; background: var(--paper); }
  .card--back {
    left: 262px; top: 653px;
    background: linear-gradient(180deg, var(--rust-light), var(--rust-dark));
    display: flex; align-items: center; justify-content: center;
  }
  .brand-name {
    font-weight: 400;
    letter-spacing: 1px;
    white-space: nowrap;
  }
  .card--front .brand-name {
    position: absolute;
    left: 0; width: 361px;
    top: 175px;
    text-align: center;
    font-size: 34px;
    color: var(--rust);
  }
  .card--back .brand-name {
    font-size: 50px;
    color: var(--gold);
  }
  .divider {
    position: absolute;
    left: 361px; top: 85px;
    width: 1px; height: 227px;
    background: var(--rule);
  }
  .details {
    position: absolute;
    left: 387px; top: 95px;
    color: var(--ink);
    font-size: 16.5px;
    line-height: 20.5px;
  }
  .person-name {
    font-weight: 700;
    font-size: 24px;
    line-height: 28px;
    color: var(--rust);
  }
  .person-role { color: var(--muted); font-size: 15.5px; line-height: 20px; }
  .address { margin-top: 21px; }
  .contact-list { list-style: none; margin-top: 13px; }
  .contact-list li { display: flex; align-items: center; gap: 12px; height: 20.5px; }
  .contact-list svg { width: 16px; height: 16px; flex: none; }
</style>
</head>
<body>
  <section class="card card--front" aria-label="Card front">
    <div class="brand-name">Dunmere Living</div>
    <div class="divider"></div>
    <div class="details">
      <div class="person-name">ELLIS HARMON</div>
      <div class="person-role">President</div>
      <address class="address" style="font-style:normal">
        4780 Cedar Bend Road<br>
        Suite #1150<br>
        Maple Ridge, TX<br>
        United States, Texas
      </address>
      <ul class="contact-list">
        <li>
          <svg viewBox="0 0 16 16" aria-hidden="true"><path fill="#b5562c" d="M3.5 1.5l2.5 0.3 1 3.2-1.6 1.2c.8 1.8 2.1 3.1 3.9 3.9l1.2-1.6 3.2 1 .3 2.5c-.3 1.2-1.3 2-2.5 2C6.3 14 2 9.7 2 4c0-1.2.8-2.2 1.5-2.5z"/></svg>
          <span>281-555-0147</span>
        </li>
        <li>
          <svg viewBox="0 0 16 16" aria-hidden="true"><rect x="1.5" y="3.5" width="13" height="9" fill="#b5562c"/><path d="M1.5 3.5L8 9l6.5-5.5" fill="none" stroke="#fff" stroke-width="1.3"/></svg>
          <span>info@Dunmere-PK.com</span>
        </li>
        <li>
          <svg viewBox="0 0 16 16" aria-hidden="true"><circle cx="8" cy="8" r="6.5" fill="#b5562c"/><ellipse cx="8" cy="8" rx="2.6" ry="6.5" fill="none" stroke="#fff" stroke-width="1"/><path d="M1.5 8h13" stroke="#fff" stroke-width="1"/></svg>
          <span>www.Dunmere-PK.com</span>
        </li>
      </ul>
    </div>
  </section>

  <section class="card card--back" aria-label="Card back">
    <div class="brand-name">Dunmere Living</div>
  </section>
</body>
</html>
```